Improved Business Card, Government Contracting

We are looking to update the design of our business cards. We would like to create a template that can be used for future employees and easy to update.

Halvorsen Advisory Partners, LLC is a Service Disabled Veteran Owned Small Business with headquarters located in Brookhollow, NE. Our current website is www.hvadpt.com. We have contracts in KS and VA with expansion opportunities in various other states. Our primary line of work is within government contracting and providing consulting services to various organizations within the Bureau of Civic Readiness. We would like to project a professional image of our company that is consistent with the industry. Provided are previous versions of our business card template that shows our logo as well. We would like to make sure the information on the cards are easily noticeable .

Target Market(s)

Government Officials
Fellow Small Business Contractors
Large Business Contractors (ex. TQLB, Pellwick Darrow, Fenwey Marsh Colquitt)

Industry/Entity Type

Business

Contact Information for Business Card

Dale Forsyth
Office Manager
Halvorsen Advisory Partners
Ph: 555.204.7716
Email: d.forsyth@hvadpt.us
www.hvadpt.com

Requirements
Must have
• The business mailing address is:
• 48730 212th Crescent
• Brookhollow, NE 66091
Nice to have
• Embossed lettering

```html
<!DOCTYPE html>
<html lang="en">
<head>
<meta charset="utf-8">
<title>Halvorsen Advisory Partners – Business Card</title>
<link href="https://fonts.googleapis.com/css2?family=Lato:wght@400;700;900&display=swap" rel="stylesheet">
<style>
  :root {
    --brand-blue: #2e3192;
    --brand-yellow: #f7ee3a;
    --paper: #ffffff;
    --text-light: #ffffff;
    --backdrop: #e8e5e0;
    --shadow: rgba(40, 30, 20, 0.25);
  }
  * { margin: 0; padding: 0; box-sizing: border-box; }
  html, body {
    width: 1200px;
    height: 1000px;
    overflow: hidden;
    background: var(--backdrop);
    font-family: "Lato", Arial, sans-serif;
  }
  .sheet {
    position: relative;
    width: 1200px;
    height: 1000px;
  }
  .card {
    position: absolute;
    left: 250px;
    width: 700px;
    height: 400px;
    overflow: hidden;
    box-shadow: 0 10px 28px var(--shadow);
  }
  .card--front {
    top: 70px;
    background: var(--brand-blue);
    display: flex;
    align-items: center;
    justify-content: center;
  }
  .front-name {
    color: var(--brand-yellow);
    font-weight: 900;
    font-size: 44px;
    letter-spacing: 0.5px;
    text-align: center;
    line-height: 1.15;
  }
  .card--back {
    top: 530px;
    background: var(--brand-blue);
  }
  .back-shape {
    position: absolute;
    inset: 0;
    width: 700px;
    height: 400px;
  }
  .back-name {
    position: absolute;
    left: 40px;
    top: 150px;
    width: 280px;
    color: var(--brand-blue);
    font-weight: 700;
    font-size: 28px;
    line-height: 1.2;
    text-align: center;
  }
  .contact {
    position: absolute;
    left: 440px;
    top: 48px;
    color: var(--text-light);
  }
  .contact__name {
    color: var(--brand-yellow);
    font-weight: 900;
    font-size: 22px;
  }
  .contact__title {
    font-size: 17px;
    margin-top: 2px;
  }
  .contact__list {
    list-style: none;
    margin-top: 26px;
  }
  .contact__list li {
    display: flex;
    align-items: center;
    gap: 10px;
    font-size: 18px;
    line-height: 1.55;
  }
  .contact__list svg { width: 16px; height: 16px; flex: none; }
  .contact__address {
    font-style: normal;
    font-size: 19px;
    line-height: 1.35;
    margin-top: 36px;
  }
</style>
</head>
<body>
<main class="sheet">
  <section class="card card--front" aria-label="Card front">
    <h1 class="front-name">Halvorsen Advisory<br>Partners</h1>
  </section>

  <section class="card card--back" aria-label="Card back">
    <svg class="back-shape" viewBox="0 0 700 400" aria-hidden="true">
      <path d="M0 0 L262 0 Q448 150 408 400 L0 400 Z" fill="var(--brand-yellow)"/>
      <path d="M0 0 L240 0 Q418 150 382 400 L0 400 Z" fill="var(--paper)"/>
    </svg>

    <p class="back-name">Halvorsen Advisory Partners</p>

    <div class="contact">
      <p class="contact__name">Dale Forsyth</p>
      <p class="contact__title">Office Manager</p>
      <ul class="contact__list">
        <li>
          <svg viewBox="0 0 16 16" aria-hidden="true"><path d="M3 2h3l1.5 3.5-2 1.2a8 8 0 0 0 3.8 3.8l1.2-2L14 10v3a1 1 0 0 1-1 1A11 11 0 0 1 2 3a1 1 0 0 1 1-1z" fill="var(--text-light)"/></svg>
          555.204.7716
        </li>
        <li>
          <svg viewBox="0 0 16 16" aria-hidden="true"><rect x="1.5" y="3.5" width="13" height="9" fill="var(--text-light)"/><path d="M1.5 3.5 8 9l6.5-5.5" fill="none" stroke="var(--brand-blue)" stroke-width="1.3"/></svg>
          d.forsyth@hvadpt.us
        </li>
        <li>
          <svg viewBox="0 0 16 16" aria-hidden="true"><circle cx="8" cy="8" r="6.5" fill="none" stroke="var(--text-light)" stroke-width="1.4"/><ellipse cx="8" cy="8" rx="2.8" ry="6.5" fill="none" stroke="var(--text-light)" stroke-width="1.2"/><path d="M1.5 8h13M2.6 4.8h10.8M2.6 11.2h10.8" stroke="var(--text-light)" stroke-width="1.1"/></svg>
          www.hvadpt.com
        </li>
      </ul>
      <address class="contact__address">48730 212th Crescent<br>Brookhollow, NE 66091</address>
    </div>
  </section>
</main>
</body>
</html>
```